Refer a Friend A5 Flyer for Healthcare Staff

We need an A5 flyer that we can hand out to existing and new staff members promoting our Refer a friend Scheme. We need the leaflet to encourage staff to talk to their family and friends about joining our Healthcare Agency, which provides staff to local care related establishments. Using our logo and brand colours blue and green, as per our website, the final design will need to clearly convey the benefits and attractions of referring additional staff to the team. In addition is the promotion of our Chatterbook page, requesting staff to like the page and to like and share various posts.

Target Market(s)

Healthcare and potential Healthcare Staff

Industry/Entity Type

Healthcare

Colors
33b8a4
3277b5

Requirements
Must have
• Company Logo, Brand colours,
• text; "Refer a Friend and receive a £50 Bonus after just 1 completed shift"
• text; "3 easy steps to refer a friend, 1 Fill out your name on the back of your Business Card 2 Hand the card to your friend or any person you wish to refer, 3 ask your friend to present the card to us when they attend their interview"
• text; "Like and share any of our Open Days on Chatterbook for a chance to win a prize, you can find us easily by searching @CarewellStaffingPartners"
• text; "Like our Page to stay up to date with our events and offers"
Nice to have
• care worker / elderly care / support worker pictures
• Content / pics from website www.carewellstaffingpartners.co.uk

```html
<!DOCTYPE html>
<html lang="en">
<head>
<meta charset="utf-8">
<title>Refer a Friend Flyer</title>
<link href="https://fonts.googleapis.com/css2?family=Montserrat:wght@400;500;700&display=swap" rel="stylesheet">
<style>
  :root {
    --teal: #33b8a4;
    --blue: #3277b5;
    --ink: #1d1d1f;
    --band: #f3f3f3;
    --red: #e3232b;
    --gold: #e8c12a;
    --stage: #8f8f8f;
    --paper: #ffffff;
  }
  * { box-sizing: border-box; margin: 0; padding: 0; }
  html, body { width: 1200px; height: 822px; overflow: hidden; }
  body {
    background: var(--stage);
    font-family: "Montserrat", Arial, sans-serif;
    position: relative;
  }
  .flyer {
    position: absolute;
    left: 321px; top: 15px;
    width: 558px; height: 792px;
    background: var(--paper);
    overflow: hidden;
  }
  .hero-photo { position: absolute; right: 0; top: 0; width: 340px; height: 352px; }
  .brand {
    position: absolute; left: 14px; top: 40px;
    display: flex; align-items: center; gap: 8px;
    color: var(--blue); font-weight: 500; font-size: 19px; line-height: 1.1;
  }
  .brand-dot { width: 22px; height: 22px; border-radius: 50%; background: var(--teal); flex: none; }
  .headline {
    position: absolute; left: 12px; top: 128px;
    font-weight: 700; font-size: 32px; line-height: 39px; letter-spacing: 1px;
  }
  .headline .blue { color: var(--blue); display: block; }
  .headline .green { color: var(--teal); display: block; }
  .steps-title {
    position: absolute; left: 13px; top: 354px;
    font-weight: 500; font-size: 21px; letter-spacing: 0.8px; color: var(--ink);
  }
  .steps-rule { position: absolute; left: 20px; top: 357px; width: 390px; height: 50px; }
  .steps-spine { position: absolute; left: 23px; top: 397px; width: 1px; height: 104px; background: var(--blue); }
  .steps { list-style: none; position: absolute; left: 16px; top: 406px; }
  .steps li {
    display: flex; align-items: center; gap: 5px;
    height: 28px; font-size: 12px; letter-spacing: 0.5px; color: var(--ink);
  }
  .step-num {
    width: 15px; height: 15px; border-radius: 50%;
    color: #fff; font-size: 10px; font-weight: 700;
    display: flex; align-items: center; justify-content: center;
  }
  .step-num.teal { background: var(--teal); }
  .step-num.blue { background: var(--blue); }
  .promo-band { position: absolute; left: 0; top: 539px; width: 558px; height: 120px; background: var(--band); }
  .promo-photo { position: absolute; left: 12px; top: 519px; width: 180px; height: 166px; }
  .trophy { position: absolute; left: 192px; top: 545px; width: 50px; height: 58px; }
  .prize-tag {
    position: absolute; left: 240px; top: 553px; width: 66px; height: 13px;
    background: var(--red); color: #fff; font-size: 8px; font-weight: 500;
    padding-left: 5px; line-height: 13px;
    clip-path: polygon(0 0, 100% 0, 92% 50%, 100% 100%, 0 100%);
  }
  .action-icons { position: absolute; left: 246px; top: 572px; width: 66px; height: 32px; }
  .promo-text {
    position: absolute; left: 315px; top: 574px;
    font-size: 12.5px; letter-spacing: 0.6px; line-height: 17px; color: var(--ink);
  }
  .promo-text .spread { word-spacing: 5px; }
  .promo-text .gap { margin-top: 4px; }
  .promo-text .handle { color: var(--teal); }
  .page-cta {
    position: absolute; left: 0; width: 558px; top: 709px;
    display: flex; justify-content: center; align-items: center; gap: 5px;
    font-size: 13px; letter-spacing: 0.6px; color: var(--ink);
  }
  .footer { position: absolute; left: 0; bottom: 0; width: 558px; height: 52px; background: var(--teal); }
  .footer-block { position: absolute; left: 0; top: 0; width: 49px; height: 52px; background: var(--blue); }
  .footer-url {
    position: absolute; left: 84px; top: 0; line-height: 52px;
    color: #fff; font-size: 21px; letter-spacing: 1px;
  }
  .globe { position: absolute; left: 63px; top: 20px; width: 12px; height: 12px; }
</style>
</head>
<body>
<article class="flyer">
  <svg class="hero-photo" viewBox="0 0 340 352" role="img" aria-label="Photo of a smiling care worker in blue scrubs hugging an elderly woman in a wheelchair">
    <defs>
      <linearGradient id="heroTone" x1="0" y1="0" x2="1" y2="1">
        <stop offset="0" stop-color="#d9c3a3"/>
        <stop offset="0.45" stop-color="#4f8fcf"/>
        <stop offset="1" stop-color="#8fc6e6"/>
      </linearGradient>
    </defs>
    <path d="M340 0 H120 C40 40 -10 150 20 210 C80 300 220 330 340 352 Z" fill="var(--teal)"/>
    <path d="M340 0 H140 C60 45 5 150 32 200 C90 285 220 312 340 335 Z" fill="url(#heroTone)"/>
  </svg>

  <div class="brand"><span class="brand-dot"></span><span>Carewell<br>Staffing Partners</span></div>

  <h1 class="headline">
    <span class="blue">Refer a</span>
    <span class="blue">Friend and</span>
    <span class="blue">receive a £50</span>
    <span class="green">Bonus after just</span>
    <span class="green">1 completed shift</span>
  </h1>

  <h2 class="steps-title">3 easy steps to refer a friend</h2>
  <svg class="steps-rule" viewBox="0 0 390 50">
    <polyline points="0,29 343,29 347,18 350,42 355,0 359,20 390,20" fill="none" stroke="var(--blue)" stroke-width="1.2"/>
  </svg>
  <div class="steps-spine"></div>
  <ol class="steps">
    <li><span class="step-num teal">1</span>Fill out your name on the back of your Business Card</li>
    <li><span class="step-num blue">2</span>Hand the card to your friend or any person you wish to refer</li>
    <li><span class="step-num teal">3</span>Ask your friend to present the card to us when they attend their interview</li>
  </ol>

  <div class="promo-band"></div>
  <svg class="promo-photo" viewBox="0 0 180 166" role="img" aria-label="Photo of a smiling care assistant holding hands with an elderly lady">
    <defs>
      <linearGradient id="promoTone" x1="0" y1="0" x2="1" y2="0">
        <stop offset="0" stop-color="#b89a82"/>
        <stop offset="0.55" stop-color="#7a5a45"/>
        <stop offset="1" stop-color="#e9eef2"/>
      </linearGradient>
    </defs>
    <path d="M60 2 C110 -6 160 30 175 70 C150 120 90 160 40 164 C10 160 0 130 2 90 C4 40 20 8 60 2 Z" fill="var(--teal)"/>
    <path d="M62 8 C108 2 152 34 166 70 C142 116 88 152 42 156 C16 152 8 126 9 90 C11 44 26 14 62 8 Z" fill="url(#promoTone)"/>
  </svg>
  <svg class="trophy" viewBox="0 0 50 58">
    <path d="M10 4 H40 V14 C40 28 32 34 25 34 C18 34 10 28 10 14 Z" fill="var(--gold)"/>
    <path d="M10 8 H3 C3 20 8 24 13 24 M40 8 H47 C47 20 42 24 37 24" fill="none" stroke="var(--gold)" stroke-width="3"/>
    <rect x="22" y="34" width="6" height="12" fill="var(--gold)"/>
    <rect x="14" y="46" width="22" height="8" rx="1" fill="var(--gold)"/>
  </svg>
  <div class="prize-tag">win a prize</div>
  <svg class="action-icons" viewBox="0 0 66 32">
    <circle cx="16" cy="16" r="15" fill="var(--teal)"/>
    <polyline points="9,16 14,21 23,11" fill="none" stroke="#fff" stroke-width="3" stroke-linecap="round" stroke-linejoin="round"/>
    <circle cx="50" cy="16" r="15" fill="var(--blue)"/>
    <path d="M42 22 C43 15 48 13 54 13 V9 L60 15 L54 21 V17 C49 17 45 18 42 22 Z" fill="#fff"/>
  </svg>
  <div class="promo-text">
    <p class="spread">any of our Open Days on</p>
    <p>Chatterbook for a chance</p>
    <p class="gap">you can find us easily by searching</p>
    <p class="handle">@CarewellStaffingPartners</p>
  </div>

  <p class="page-cta">
    <svg width="17" height="15" viewBox="0 0 17 15"><rect x="0" y="6" width="4" height="9" fill="var(--blue)"/><path d="M5 6 L9 0 C11 0 11 2 10.5 5 H16 C17 5 17 7 16 7.5 C17 8.5 16.5 10 15.5 10 C16 11 15.5 12.5 14.5 12.5 C14.8 14 14 15 13 15 H5 Z" fill="var(--blue)"/></svg>
    our Page to stay up to date with our events and offers
  </p>

  <footer class="footer">
    <div class="footer-block"></div>
    <svg class="globe" viewBox="0 0 12 12"><circle cx="6" cy="6" r="5.5" fill="none" stroke="#fff"/><ellipse cx="6" cy="6" rx="2.4" ry="5.5" fill="none" stroke="#fff"/><line x1="0.5" y1="6" x2="11.5" y2="6" stroke="#fff"/></svg>
    <span class="footer-url">www.carewellstaffingpartners.co.uk</span>
  </footer>
</article>
</body>
</html>
```